Cozy Cradle Loops Needs a Beautiful Website

I need a new website for this new E-commerce. I sell handmade baby crochets, e.g. booties, headbands, hats, etc. I need a feminine and soft design to make the moms-to-be say 'oohh ahh'. I'd like pink, blue and gray. I'd like an inviting homepage, and nice regular pages where people can see and order the products.

Industry/Entity Type

Baby

Requirements
Must have
• beautiful, soft, feminine design. Please use pictures of the colors I'd like: brown, yellow, pink and blue. Any combination, but definitely include brown.

```html
<!DOCTYPE html>
<html lang="en">
<head>
<meta charset="utf-8">
<title>Cozy Cradle Loops</title>
<link href="https://fonts.googleapis.com/css2?family=Dancing+Script:wght@600;700&family=Open+Sans:wght@400;600;700&display=swap" rel="stylesheet">
<style>
:root{
  --bg:#c4e5f4;
  --cream:#fbf6ec;
  --pink:#ee6f96;
  --blue:#5bb8e0;
  --blue-dark:#3a9ccb;
  --yellow:#fbefb0;
  --mint:#cfeee3;
  --rose:#fbd3df;
  --gray:#6f6f6f;
  --line:#e4e4e4;
  --white:#ffffff;
}
*{box-sizing:border-box;margin:0;padding:0}
html,body{width:726px;height:1200px;overflow:hidden}
body{
  background:var(--bg);
  font-family:"Open Sans",Arial,sans-serif;
  color:var(--gray);
  position:relative;
}
.page{position:absolute;left:76px;top:12px;width:574px;height:1170px}

/* header */
.site-header{height:98px;background:var(--cream);border-radius:4px 4px 0 0;display:flex;align-items:center;justify-content:center}
.brand-name{font-family:"Dancing Script",cursive;font-weight:700;font-size:26px;color:var(--pink);line-height:1}

.main-nav{height:22px;background:var(--blue);display:flex;justify-content:space-between;align-items:center;padding:0 16px}
.main-nav a{font-family:"Dancing Script",cursive;font-weight:700;font-size:14px;color:var(--white);text-decoration:none}

.hero{margin:6px 8px 0;height:258px;border-radius:4px;background:linear-gradient(120deg,#e8d9c8 0%,#f3e2cf 40%,#c9d8e6 70%,#b9dbc9 100%)}
.hero-dots{display:flex;justify-content:center;gap:5px;margin-top:-14px;position:relative}
.hero-dots span{width:6px;height:6px;border-radius:50%;background:var(--white);opacity:.7}
.hero-dots span.on{background:var(--blue-dark);opacity:1}

/* features */
.features{display:flex;gap:14px;margin-top:16px;padding:0 4px}
.feature{flex:1;height:96px;border-radius:4px;text-align:center;padding-top:26px;border-bottom:6px solid var(--white)}
.feature.pink{background:var(--rose)}
.feature.yellow{background:var(--yellow)}
.feature.mint{background:var(--mint)}
.feature h3{font-family:"Dancing Script",cursive;font-size:21px;color:var(--pink);font-weight:700;white-space:nowrap}
.feature.yellow h3{color:#d98a3a;font-size:19px}
.feature.mint h3{color:#3a9c84}
.feature p{font-size:8px;color:var(--gray);margin-top:2px}

/* sections */
.row{display:flex;gap:14px;margin-top:22px;padding:0 4px}
.row.second{margin-top:30px}
.section-title{font-family:"Dancing Script",cursive;font-weight:700;font-size:19px;color:var(--pink);border-bottom:1px solid var(--line);padding-bottom:2px;margin-bottom:8px}
.section-title span{color:var(--blue-dark)}
.products{width:378px}
.product-grid{display:flex;gap:10px}
.product{flex:1;text-align:center}
.product h4{font-family:"Dancing Script",cursive;font-size:14px;color:var(--gray);font-weight:700;margin-bottom:3px}
.thumb{height:92px;border-radius:3px;border:3px solid var(--white);box-shadow:0 0 0 1px var(--line)}
.t-pink{background:linear-gradient(135deg,#f4c4d2,#e28aa5)}
.t-blue{background:linear-gradient(135deg,#8fa1b4,#4b5d72)}
.t-red{background:linear-gradient(135deg,#e1d4cc,#c94b5d)}
.t-ivory{background:linear-gradient(135deg,#f1ead9,#b9a78f)}
.t-rose{background:linear-gradient(135deg,#fbe1ea,#ee97b1)}
.t-mix{background:linear-gradient(135deg,#e2736f,#8ccbb6 55%,#f2d17a)}
.buy{display:flex;gap:4px;margin-top:5px}
.buy span{flex:1;height:12px;font-size:6px;line-height:12px;color:var(--white);background:var(--gray);border-radius:2px;font-weight:600}
.buy span.add{background:var(--pink)}
.price{display:flex;justify-content:space-between;align-items:center;margin-top:5px;font-size:7px}
.price b{background:var(--blue);color:var(--white);padding:1px 8px;border-radius:2px;font-size:7px}

.sidebar{flex:1}
.categories{list-style:none;background:var(--white);border-radius:3px;padding:4px 8px}
.categories li{font-family:"Dancing Script",cursive;font-size:12px;padding:4px 0;border-bottom:1px solid var(--line);color:var(--gray)}
.categories li:last-child{border-bottom:0}
.categories li.active{color:var(--pink)}
.sale{height:160px;border-radius:4px;margin-top:6px;background:linear-gradient(135deg,#7ccbea,#4fb0dc);color:var(--white);text-align:center;padding-top:30px}
.sale p{font-size:19px;font-weight:700}
.sale strong{display:block;font-size:44px;line-height:1.05}
.sale a{display:inline-block;margin-top:8px;font-family:"Dancing Script",cursive;font-size:13px;color:var(--white);border-bottom:1px solid var(--white);text-decoration:none}

/* blog */
.blog{margin-top:36px;padding:0 4px}
.blog-row{display:flex;gap:10px;align-items:stretch}
.blog-photo{width:120px;height:160px;border-radius:4px}
.p-baby{background:linear-gradient(160deg,#f5d8c6,#e8a9a2)}
.p-towel{background:linear-gradient(160deg,#b9e3f3,#78c0dd)}
.post{flex:1;background:var(--white);border-radius:4px;padding:10px 10px}
.post h4{font-family:"Dancing Script",cursive;font-size:15px;color:var(--pink);font-weight:700}
.post p{font-size:7px;line-height:1.5;margin-top:4px}
.post a{display:inline-block;margin-top:8px;font-family:"Dancing Script",cursive;font-size:12px;color:var(--pink);text-decoration:none}

.site-footer{position:absolute;left:4px;right:4px;bottom:6px;display:flex;justify-content:space-between;align-items:center;font-size:7px;color:#4d7e95}
.social{display:flex;gap:4px}
.social span{width:13px;height:13px;border-radius:50%;background:var(--blue-dark)}
.social span:nth-child(2){background:#5ab8e6}
.social span:nth-child(3){background:var(--pink)}
.social span:nth-child(4){background:#f2a33a}
</style>
</head>
<body>
<div class="page">
  <header class="site-header">
    <div class="brand-name">Cozy Cradle Loops</div>
  </header>
  <nav class="main-nav">
    <a href="#">Home</a><a href="#">About Us</a><a href="#">Booties</a><a href="#">Handmade</a><a href="#">Blog</a><a href="#">Contact Us</a>
  </nav>

  <div class="hero" role="img" aria-label="Photo of a smiling baby lying on a crocheted blanket"></div>
  <div class="hero-dots"><span></span><span class="on"></span><span></span><span></span><span></span></div>

  <section class="features">
    <div class="feature pink"><h3>Size Shopping</h3><p>View Our New Arrivals</p></div>
    <div class="feature yellow"><h3>Shopping Information</h3><p>How Fast Can We Ship</p></div>
    <div class="feature mint"><h3>Read Our Blog</h3><p>Our Latest News and Info</p></div>
  </section>

  <div class="row">
    <section class="products">
      <h2 class="section-title">Latest <span>Products</span></h2>
      <div class="product-grid">
        <div class="product"><h4>Pink Bootie</h4><div class="thumb t-pink" role="img" aria-label="Pink crochet booties"></div><div class="buy"><span>ADD TO WISH</span><span class="add">ADD TO CART</span></div><div class="price">Rs.000.00<b>View</b></div></div>
        <div class="product"><h4>Sneaker Blue</h4><div class="thumb t-blue" role="img" aria-label="Blue crochet sneakers"></div><div class="buy"><span>ADD TO WISH</span><span class="add">ADD TO CART</span></div><div class="price">Rs.000.00<b>View</b></div></div>
        <div class="product"><h4>Sneaker Glory</h4><div class="thumb t-red" role="img" aria-label="Red crochet sneakers"></div><div class="buy"><span>ADD TO WISH</span><span class="add">ADD TO CART</span></div><div class="price">Rs.000.00<b>View</b></div></div>
      </div>
    </section>
    <aside class="sidebar">
      <h2 class="section-title">Product <span>Categories</span></h2>
      <ul class="categories">
        <li class="active">Baby girl</li><li>Baby boy</li><li>Newborn</li><li>Shoes</li><li>Accessories</li><li>Toys</li>
      </ul>
    </aside>
  </div>

  <div class="row second">
    <section class="products">
      <h2 class="section-title">Featured <span>Products</span></h2>
      <div class="product-grid">
        <div class="product"><h4>Ivory Shoes</h4><div class="thumb t-ivory" role="img" aria-label="Ivory crochet baby shoes"></div><div class="buy"><span>ADD TO WISH</span><span class="add">ADD TO CART</span></div><div class="price">Rs.000.00<b>View</b></div></div>
        <div class="product"><h4>Pink Cover</h4><div class="thumb t-rose" role="img" aria-label="Pink crochet cover"></div><div class="buy"><span>ADD TO WISH</span><span class="add">ADD TO CART</span></div><div class="price">Rs.000.00<b>View</b></div></div>
        <div class="product"><h4>Games</h4><div class="thumb t-mix" role="img" aria-label="Colourful crochet toys"></div><div class="buy"><span>ADD TO WISH</span><span class="add">ADD TO CART</span></div><div class="price">Rs.000.00<b>View</b></div></div>
      </div>
    </section>
    <aside class="sidebar">
      <div class="sale"><p>Sale UpTO</p><strong>50%</strong><a href="#">Shop Now</a></div>
    </aside>
  </div>

  <section class="blog">
    <h2 class="section-title">Our <span>Blog</span></h2>
    <div class="blog-row">
      <div class="blog-photo p-baby" role="img" aria-label="Photo of a baby in a pink crochet hat"></div>
      <article class="post"><h4>Special Gift</h4><p>Soft handmade booties make a sweet gift for every new mom. Find the perfect pair in our new spring colours.</p><a href="#">Read More</a></article>
      <article class="post"><h4>Special Gift</h4><p>Our crochet hats are made with gentle yarn in pink, blue and brown to keep little heads warm.</p><a href="#">Read More</a></article>
      <div class="blog-photo p-towel" role="img" aria-label="Photo of a baby wrapped in a blue towel"></div>
    </div>
  </section>

  <footer class="site-footer">
    <span>Copyright 2014 Cozy Cradle Loops. All Rights Reserved.</span>
    <div class="social"><span></span><span></span><span></span><span></span></div>
  </footer>
</div>
</body>
</html>
```